Walk Beside The River

Business Card design

Target Market(s)

People who require support in the commnity

Industry/Entity Type

Mental Health Support

Contact Information for Business Card

Mental Health Support Rosalind Tavener walkbesidetheriver@mailcove.com.au 0481 637 092 PO Box 926 Larkfield NSW 2873

Colors
6B429C
8869AF
B7A5CE
E3DAEB
F3F0F8

Requirements
Must have
• Logo & details listed above
Should not have
• No red or orange

```html
<!DOCTYPE html>
<html lang="en">
<head>
<meta charset="utf-8">
<title>Walk Beside The River — Business Card</title>
<link rel="stylesheet" href="https://fonts.googleapis.com/css2?family=Open+Sans:wght@400;600;800&display=swap">
<style>
  :root {
    --ink: #1f1e23;
    --purple: #6B429C;
    --purple-mid: #8869AF;
    --lilac: #B7A5CE;
    --mist: #E3DAEB;
    --paper: #F3F0F8;
    --yellow: #f2e62a;
    --white: #ffffff;
    --stage: #e9e6ee;
  }
  * { box-sizing: border-box; margin: 0; padding: 0; }
  html, body { width: 1200px; height: 780px; overflow: hidden; }
  body {
    background: var(--stage);
    font-family: "Open Sans", sans-serif;
    display: flex;
    align-items: center;
    justify-content: center;
    gap: 40px;
  }
  .card {
    position: relative;
    width: 540px;
    height: 320px;
    border-radius: 22px;
    overflow: hidden;
    border: 3px solid var(--yellow);
  }

  /* Front */
  .card-front { background: var(--ink); color: var(--white); }
  .brand {
    position: absolute;
    left: 34px; top: 26px;
    display: flex; align-items: center; gap: 12px;
  }
  .brand-dot {
    width: 58px; height: 58px; border-radius: 50%;
    background: var(--purple);
  }
  .brand-name {
    font-weight: 600; font-size: 15px; letter-spacing: 1.5px;
    text-transform: uppercase; color: var(--yellow);
  }
  .person {
    position: absolute; left: 0; top: 104px;
    padding-left: 34px;
  }
  .person-marker {
    position: absolute; left: 0; top: 6px;
    width: 22px; height: 30px; background: var(--yellow);
  }
  .person-name { font-weight: 800; font-size: 28px; line-height: 1.2; }
  .person-name .first { color: var(--yellow); }
  .person-name .last { color: var(--purple-mid); }
  .person-role { font-size: 14px; margin-top: 2px; }
  .contacts {
    position: absolute; left: 22px; top: 186px;
    list-style: none; font-size: 13px; line-height: 1.55;
  }
  .contacts li { display: flex; align-items: center; gap: 8px; }
  .contacts svg { width: 13px; height: 13px; flex: none; }
  .service {
    position: absolute; right: 36px; bottom: 62px;
    text-align: right; font-size: 16px; line-height: 1.3;
  }
  .edge-band { position: absolute; left: 0; bottom: 0; width: 100%; height: 44px; }

  /* Back */
  .card-back { background: var(--purple); }
  .back-pattern {
    position: absolute; inset: 0;
    background: linear-gradient(125deg, var(--purple) 0%, #7450a6 55%, var(--purple-mid) 85%, var(--lilac) 100%);
  }
  .back-brand {
    position: absolute; right: 110px; bottom: 70px;
    display: flex; align-items: center; gap: 8px;
  }
  .back-brand .brand-dot { width: 18px; height: 18px; background: var(--yellow); }
  .back-brand .brand-name { font-size: 12px; color: var(--white); }
</style>
</head>
<body>

  <section class="card card-front">
    <div class="brand">
      <span class="brand-dot"></span>
      <span class="brand-name">Walk Beside The River</span>
    </div>

    <div class="person">
      <span class="person-marker"></span>
      <h1 class="person-name"><span class="first">Danica</span> <span class="last">Holloway</span></h1>
      <p class="person-role">CEO/Director</p>
    </div>

    <ul class="contacts">
      <li>
        <svg viewBox="0 0 16 16"><path fill="#f2e62a" d="M3.6 1.5l2.3 2.4-1.3 1.7c.9 2 2.6 3.7 4.6 4.6l1.7-1.3 2.4 2.3-1.2 2.3C6.8 13.5 2.5 9.2 1.3 2.7z"/></svg>
        0481 637 092
      </li>
      <li>
        <svg viewBox="0 0 16 16"><rect x="1.5" y="3.5" width="13" height="9" rx="1.5" fill="none" stroke="#f2e62a" stroke-width="1.6"/><path d="M2 4.5l6 4.5 6-4.5" fill="none" stroke="#f2e62a" stroke-width="1.6"/></svg>
        walkbesidetheriver@mailcove.com.au
      </li>
      <li>
        <svg viewBox="0 0 16 16"><path fill="#f2e62a" d="M8 1a5 5 0 0 0-5 5c0 3.6 5 9 5 9s5-5.4 5-9a5 5 0 0 0-5-5zm0 7a2 2 0 1 1 0-4 2 2 0 0 1 0 4z"/></svg>
        PO Box 926 Larkfield NSW 2873
      </li>
    </ul>

    <p class="service">Mental Health Support<br>Rosalind Tavener</p>

    <svg class="edge-band" viewBox="0 0 540 44" preserveAspectRatio="none">
      <polygon points="0,24 340,24 340,44 0,44" fill="#6B429C"/>
      <polygon points="0,20 340,20 340,23 0,23" fill="#f2e62a"/>
      <polygon points="338,14 540,14 540,44 348,44" fill="#f2e62a"/>
    </svg>
  </section>

  <section class="card card-back">
    <div class="back-pattern" role="img" aria-label="Repeating pattern of small sparkle stars on purple, brightening toward the right"></div>
    <div class="back-brand">
      <span class="brand-dot"></span>
      <span class="brand-name">Walk Beside The River</span>
    </div>
  </section>

</body>
</html>
```